Business Card Design Project - Sports Brand

Brisk is a e-commerce fitness wear brand for ladies who are into gym, pole and swim.

Card should not be overly cluttered and should include the following:

1. logo
2. Name of the company (Use "Brisk Loom Pte Ltd" for now)
3. Address of company (Use a mock address)
4. Representative's name and contact info etc. (use a mock name and contact info)
5. website address

Target Market(s)

Women who are into pole , gym, and swim.

Women who shop online

Industry/Entity Type

E-Commerce

Colors

Designer to choose colors to be used in the design.

Requirements
Nice to have
• feminine sublimation of colours

Need not be printed on traditional paper. We would like the design to be revolutionary and interesting to the eye :)
Should not have
• the design should not be traditional looking. Do not include illustrations of Bikinis, yoga poses etc. in the card.

```html
<!DOCTYPE html>
<html lang="en">
<head>
<meta charset="utf-8">
<title>Brisk Loom – Business Card</title>
<link href="https://fonts.googleapis.com/css2?family=Crimson+Text:wght@400;600&display=swap" rel="stylesheet">
<style>
  :root {
    --backdrop: #8c8883;
    --card: #ffffff;
    --brand-red: #b3213a;
    --accent-pink: #e04a82;
    --mark-pink: #e8507a;
    --text-grey: #666262;
    --shadow: rgba(0, 0, 0, 0.35);
  }
  * { margin: 0; padding: 0; box-sizing: border-box; }
  html, body {
    width: 1200px;
    height: 1000px;
    overflow: hidden;
    background: var(--backdrop);
    font-family: "Crimson Text", Georgia, serif;
  }
  .stage {
    width: 1200px;
    height: 1000px;
    display: flex;
    flex-direction: column;
    align-items: center;
    justify-content: center;
    gap: 60px;
  }
  .card {
    width: 700px;
    height: 400px;
    background: var(--card);
    box-shadow: 0 6px 18px var(--shadow);
    position: relative;
  }

  /* Front */
  .card-front {
    display: flex;
    align-items: center;
    justify-content: center;
    gap: 28px;
  }
  .brand-dot {
    border-radius: 50%;
    background: var(--mark-pink);
    flex: none;
  }
  .card-front .brand-dot { width: 190px; height: 190px; }
  .brand-block { display: flex; flex-direction: column; }
  .brand-name {
    color: var(--brand-red);
    font-weight: 600;
    line-height: 1;
  }
  .card-front .brand-name { font-size: 92px; }
  .descriptor {
    color: var(--text-grey);
    font-weight: 400;
    letter-spacing: 1px;
  }
  .card-front .descriptor { font-size: 28px; margin-top: 6px; }

  /* Back */
  .card-back {
    display: flex;
    align-items: center;
    padding: 0 50px;
    gap: 44px;
  }
  .back-brand { display: flex; align-items: center; gap: 16px; }
  .card-back .brand-dot { width: 110px; height: 110px; }
  .card-back .brand-name { font-size: 56px; }
  .card-back .descriptor { font-size: 18px; margin-top: 4px; }

  .contact { display: flex; flex-direction: column; }
  .person-name {
    color: var(--accent-pink);
    font-size: 26px;
    font-weight: 400;
    letter-spacing: 1px;
    text-transform: uppercase;
    line-height: 1.1;
  }
  .person-role { color: var(--text-grey); font-size: 21px; margin-bottom: 12px; }
  .contact-list { list-style: none; margin-bottom: 16px; }
  .contact-item {
    display: flex;
    align-items: center;
    gap: 10px;
    color: var(--text-grey);
    font-size: 20px;
    line-height: 1.6;
  }
  .contact-icon { width: 22px; height: 22px; flex: none; }
  .company-name {
    color: var(--accent-pink);
    font-size: 22px;
    letter-spacing: 1px;
    text-transform: uppercase;
  }
  .company-address { color: var(--text-grey); font-size: 20px; line-height: 1.3; font-style: normal; }
</style>
</head>
<body>
<main class="stage">

  <section class="card card-front" aria-label="Card front">
    <span class="brand-dot" aria-hidden="true"></span>
    <div class="brand-block">
      <span class="brand-name">Brisk</span>
      <span class="descriptor">Activewear Online</span>
    </div>
  </section>

  <section class="card card-back" aria-label="Card back">
    <div class="back-brand">
      <span class="brand-dot" aria-hidden="true"></span>
      <div class="brand-block">
        <span class="brand-name">Brisk</span>
        <span class="descriptor">Activewear Online</span>
      </div>
    </div>

    <div class="contact">
      <h1 class="person-name">Mara Lin</h1>
      <p class="person-role">Director</p>
      <ul class="contact-list">
        <li class="contact-item">
          <svg class="contact-icon" viewBox="0 0 22 22" aria-hidden="true">
            <circle cx="11" cy="11" r="11" fill="var(--accent-pink)"/>
            <path d="M7.5 6 L9.5 6 L10.3 8.6 L9 9.6 Q10.2 12 12.4 13 L13.4 11.7 L16 12.5 L16 14.5 Q15.5 16 13.8 15.8 Q7.2 14.8 6.2 8.2 Q6 6.5 7.5 6 Z" fill="#fff"/>
          </svg>
          555 210 4830
        </li>
        <li class="contact-item">
          <svg class="contact-icon" viewBox="0 0 22 22" aria-hidden="true">
            <circle cx="11" cy="11" r="11" fill="var(--accent-pink)"/>
            <rect x="5.5" y="7" width="11" height="8" fill="#fff"/>
            <path d="M5.5 7 L11 11.5 L16.5 7" fill="none" stroke="var(--accent-pink)" stroke-width="1.2"/>
          </svg>
          mara@briskloom.com
        </li>
        <li class="contact-item">
          <svg class="contact-icon" viewBox="0 0 22 22" aria-hidden="true">
            <circle cx="11" cy="11" r="11" fill="var(--accent-pink)"/>
            <g fill="none" stroke="#fff" stroke-width="1.2">
              <circle cx="11" cy="11" r="5.5"/>
              <ellipse cx="11" cy="11" rx="2.4" ry="5.5"/>
              <line x1="5.5" y1="11" x2="16.5" y2="11"/>
            </g>
          </svg>
          www.briskloom.com
        </li>
      </ul>
      <p class="company-name">Brisk Loom Pte. Ltd.</p>
      <address class="company-address">Shop 88, Keppel Lane,<br>Singapore 409115</address>
    </div>
  </section>

</main>
</body>
</html>
```